Letterhead for a German Distribution/Manufacturing Company

We need a professional Letterhead in a unique Design.
not to playful.
The Letterhead has to show show that we are a international company with headquater in Germany.
all details like adress, Vat Tax Number, Bank Accout, Eori, email, Company number has to be on the Letterhead.
for example use: VAT TAX DE5470318 Bank Account: Kestrel Bank IBAN DE412058731ß204683 Swift: MORV0417352 EORI 3150428697 Company Number: HRB 51806 Adress: VOLMINTA UG Ahornweg 7 Postal Code 06384 City Kelmbach Country: Germany Email: info@volminta-example.com
the design can be colored but doesnt have to be
Industry/Entity Type
Manufacturing and international distribution
Requirements
Must have
- show that we are a international company with headquater in Germany. our company infos and logo

```html
<!DOCTYPE html>
<html lang="en">
<head>
<meta charset="utf-8">
<title>VOLMINTA Letterhead</title>
<link rel="stylesheet" href="https://fonts.googleapis.com/css2?family=Lato:wght@400;700&family=Satisfy&display=swap">
<style>
  :root {
    --backdrop: #e9e9ea;
    --paper: #ffffff;
    --ink: #2b2b2b;
    --ink-soft: #3a3a3a;
    --rule: #444444;
    --logo: #4a4a4a;
  }
  * { box-sizing: border-box; margin: 0; padding: 0; }
  html, body {
    width: 1200px; height: 874px; overflow: hidden;
    background: var(--backdrop);
  }
  body {
    display: flex; align-items: center; justify-content: center;
    font-family: "Lato", Arial, sans-serif; color: var(--ink);
  }
  .letterhead {
    position: relative;
    width: 594px; height: 840px;
    background: var(--paper);
    box-shadow: 0 2px 10px rgba(0,0,0,0.12);
  }
  .brand {
    position: absolute; left: 48px; top: 58px;
    display: flex; align-items: center; gap: 10px;
  }
  .brand-dot {
    width: 30px; height: 30px; border-radius: 50%;
    background: var(--logo);
  }
  .brand-name {
    font-size: 30px; font-weight: 400; letter-spacing: 1px;
    color: var(--logo);
  }
  .meta {
    position: absolute; left: 62px; top: 176px;
    font-size: 10.5px; line-height: 1.32; color: var(--ink-soft);
  }
  .meta p + p { margin-top: 10px; }
  .salutation {
    position: absolute; left: 62px; top: 296px;
    font-size: 13px; font-weight: 700;
  }
  .body-copy {
    position: absolute; left: 62px; top: 330px; width: 470px;
    font-size: 10.5px; line-height: 1.3; color: var(--ink-soft);
  }
  .body-copy p + p { margin-top: 13px; }
  .closing {
    position: absolute; left: 62px; top: 572px;
    font-size: 10.5px; color: var(--ink-soft);
  }
  .signature {
    position: absolute; left: 72px; top: 590px;
    font-family: "Satisfy", "Brush Script MT", cursive; font-size: 32px; color: var(--ink);
  }
  .footer-rule {
    position: absolute; left: 62px; right: 0; top: 652px;
    border-top: 1.5px solid var(--rule);
  }
  .company-details {
    position: absolute; left: 0; right: 0; top: 666px;
    text-align: center; font-size: 9.5px; line-height: 1.45; color: var(--ink);
  }
</style>
</head>
<body>
  <main class="letterhead">
    <header class="brand">
      <span class="brand-dot"></span>
      <span class="brand-name">VOLMINTA</span>
    </header>

    <section class="meta">
      <p>January-03-2020</p>
      <p>Mr. Tobias Reed<br>President</p>
      <p>Arden Works<br>123 Street Name, Suite# 10<br>City, State, 120023</p>
    </section>

    <h1 class="salutation">Dear Mr. Reed</h1>

    <section class="body-copy">
      <p>Lorem ipsum dolor sit amet, consectetur adipisicing elit, sed do eiusmod tempor incididunt ut labore et dolore magna aliqua. Ut enim ad minim veniam, quis nostrud exercitation ullamco laboris nisi ut aliquip ex ea commodo consequat. Duis aute irure dolor in reprehenderit in voluptate velit esse cillum dolore eu fugiat nulla pariatur.</p>
      <p>Lorem ipsum dolor sit amet, consectetur adipisicing elit, sed do eiusmod tempor incididunt ut labore et dolore magna aliqua. Ut enim ad minim veniam, quis nostrud exercitation ullamco laboris nisi ut aliquip ex ea commodo consequat. Duis aute irure dolor in reprehenderit in voluptate velit esse cillum dolore eu fugiat nulla pariatur.</p>
      <p>Lorem ipsum dolor sit amet, consectetur adipisicing elit, sed do eiusmod tempor incididunt ut labore et dolore magna aliqua. Ut enim ad minim veniam, quis nostrud exercitation ullamco laboris nisi ut aliquip ex ea commodo consequat.</p>
      <p>Excepteur sint occaecat cupidatat non proident, sunt in culpa qui officia deserunt mollit anim id est laborum. re et dolore magnam aliquam quaerat voluptatem.</p>
    </section>

    <p class="closing">Regards</p>
    <p class="signature">Lena Hartwig</p>

    <div class="footer-rule"></div>

    <footer class="company-details">
      VAT TAX DE5470318<br>
      Bank Account: Kestrel Bank IBAN DE412058731ß204683 Swift: MORV0417352<br>
      EORI 3150428697<br>
      Company Number: HRB 51806<br>
      Adress: VOLMINTA UG Ahornweg 7 Postal Code 06384 City Kelmbach Country<br>
      Germany Email: info@volminta-example.com
    </footer>
  </main>
</body>
</html>
```